Business card design needed

The company name is Pellow Architects. We are an architectural company based in Melbourne,Australia that has a mix of client base from health care, commercial office, aged care, multi-residential, single residential and retail. Design type is contemporary.

Suggest the base colours need to be black and white. Please leave an area on the back of the card available for handwritten notes.

Target Market(s)

Generally corporate, aged 30 to 65

Industry/Entity Type

Residential

Contact Information for Business Card

Pellow Architects
Dale Pellow
14 Mosley Street
Fenwick Vale VIC 3074
T (03) 9572 4016
M 0437 619 258
E dp@pellowarc.com.au

Logo Text

PA

Logo styles of interest
Emblem Logo
Abstract Logo
Lettermark Logo
Requirements
Must have
• I am having trouble attaching a sketch so would really appreciate your effort to try the following brief.

Black and White (B&W)
Would like different card cutout profile. Logo Example, use the half circle curve of the G to form the left edge of the card with no margin. The A is to sit inside the G, connected to the G by its horizontal. The A has its cross bar and lower right leg removed. Card in black, text in white.

Back of card to be black text on white background with services provided.

Client Focused Service
Architecture and Design
Functional Planning
Town Planning
Feasability Studies
Contract Documentation
Contract Administration
Project Management

Simple elegant text, Ariel or similar
Nice to have
• Integrated logo and card cut-out.

Card base black on front, white on back
Should not have
• Too many colours
Fussy details

```html
<!DOCTYPE html>
<html lang="en">
<head>
<meta charset="utf-8">
<title>Pellow Architects — Business Card</title>
<link rel="stylesheet" href="https://fonts.googleapis.com/css2?family=Arimo:wght@400&family=Open+Sans:wght@400&display=swap">
<style>
  :root {
    --stage: #e9e7e4;
    --card-black: #0d0d0d;
    --card-charcoal: #2a2a2a;
    --ink-white: #ffffff;
    --ink-black: #111111;
    --paper: #ffffff;
    --paper-edge: #cfcfcf;
    --rule: #222222;
  }
  * { box-sizing: border-box; margin: 0; padding: 0; }
  html, body {
    width: 1200px; height: 922px; overflow: hidden;
    background: var(--stage);
  }
  .canvas { position: relative; width: 1200px; height: 922px; }

  /* ---------- Front of card ---------- */
  .card-front {
    position: absolute; left: 60px; top: 50px;
    width: 720px; height: 420px;
    border-radius: 20px; overflow: hidden;
    background: radial-gradient(ellipse at 45% 35%, var(--card-charcoal) 0%, #161616 55%, var(--card-black) 100%);
    box-shadow: 0 10px 24px rgba(0,0,0,.25);
  }
  .plan-texture {
    position: absolute; right: 0; top: 0;
    width: 420px; height: 220px;
    background: radial-gradient(ellipse at 70% 20%, rgba(255,255,255,.09) 0%, rgba(255,255,255,.03) 45%, rgba(255,255,255,0) 75%);
  }
  .brand-name {
    position: absolute; left: 48px; top: 158px;
    font-family: "Arimo", Arial, sans-serif; font-size: 36px; font-weight: 400;
    color: var(--ink-white); letter-spacing: .2px;
  }
  .name-tag {
    position: absolute; right: 0; top: 214px;
    width: 250px; height: 58px;
    background: var(--ink-white);
    display: flex; align-items: center; padding-left: 28px;
    font-family: "Open Sans", Arial, sans-serif; font-size: 24px;
    color: var(--ink-black);
  }
  .contact {
    position: absolute; right: 24px; top: 290px;
    font-family: "Open Sans", Arial, sans-serif; font-size: 18px;
    font-style: normal;
    color: var(--ink-white); text-align: right; line-height: 1;
  }
  .contact-line {
    display: flex; justify-content: flex-end; align-items: center;
    gap: 12px; height: 27px;
  }
  .contact-line svg { width: 18px; height: 18px; fill: var(--ink-white); }

  /* ---------- Back of card ---------- */
  .card-back {
    position: absolute; left: 500px; top: 500px;
    width: 640px; height: 370px;
    border-radius: 18px; overflow: hidden;
    background: radial-gradient(ellipse at 50% 40%, var(--paper) 45%, #efefef 75%, var(--paper-edge) 100%);
    box-shadow: 0 10px 24px rgba(0,0,0,.25);
  }
  .note-lines { position: absolute; left: 100px; right: 70px; top: 78px; }
  .note-line {
    height: 0; border-top: 2px dotted var(--rule);
    margin-bottom: 62px;
  }
  .back-band {
    position: absolute; left: 0; right: 0; bottom: 0; height: 78px;
    background: var(--card-black);
    display: flex; align-items: center; padding-left: 36px;
    font-family: "Arimo", Arial, sans-serif; font-size: 20px;
    color: var(--ink-white);
  }
</style>
</head>
<body>
<main class="canvas">

  <section class="card-front" aria-label="Business card front">
    <div class="plan-texture" role="img" aria-label="Faint architectural floor plan linework in the background"></div>
    <div class="brand-name">Pellow Architects</div>
    <div class="name-tag">Dale Pellow</div>

    <address class="contact">
      <div class="contact-line">14 Mosley Street Fenwick Vale VIC 3074</div>
      <div class="contact-line">
        <svg viewBox="0 0 24 24" aria-hidden="true"><path d="M3 9c0-3 4-5 9-5s9 2 9 5v2h-5V9c-1-1-7-1-8 0v2H3z M6 12h12l2 8H4z"/></svg>
        <span>(03) 9572 4016</span>
      </div>
      <div class="contact-line">
        <svg viewBox="0 0 24 24" aria-hidden="true"><path d="M7 2h10a1 1 0 0 1 1 1v18a1 1 0 0 1-1 1H7a1 1 0 0 1-1-1V3a1 1 0 0 1 1-1zm1 3v10h8V5zm4 12a1.5 1.5 0 1 0 0 3 1.5 1.5 0 0 0 0-3z"/></svg>
        <span>0437 619 258</span>
      </div>
      <div class="contact-line">
        <svg viewBox="0 0 24 24" aria-hidden="true"><path d="M2 5h20v14H2zm2 2v.5l8 5.5 8-5.5V7zm0 3v7h16v-7l-8 5.5z"/></svg>
        <span>dp@pellowarc.com.au</span>
      </div>
    </address>
  </section>

  <section class="card-back" aria-label="Business card back">
    <div class="note-lines">
      <div class="note-line"></div>
      <div class="note-line"></div>
      <div class="note-line"></div>
      <div class="note-line"></div>
    </div>
    <div class="back-band">Pellow Architects</div>
  </section>

</main>
</body>
</html>
```